Looking for a modern, Professional business card design

We have a simple business card, but are looking for a more modern, professional look. A sample of the basic card is attached as well as the logo. We would also like to add that we offer:
Struggling with your finances?
- Learn to become debt free
- Discover the power of cash
- Control your money instead of it controlling you
Let us help you achieve a new level of financial freedom!
Also, we would like to have a "SPECIAL OFFER!: FREE 30 minute consultation"
Financial Planning

```html
<!DOCTYPE html>
<html lang="en">
<head>
<meta charset="utf-8">
<title>Liberty Money Coaching – Business Card</title>
<link href="https://fonts.googleapis.com/css2?family=Roboto:wght@400;700;900&display=swap" rel="stylesheet">
<style>
  :root {
    --page-bg: #d9d6d1;
    --card-bg: #eef0ec;
    --green-dark: #2c7419;
    --green-mid: #4f9a22;
    --green-light: #8cc63f;
    --brand-green: #2f7d1f;
    --ink-light: #f3f7ec;
    --ink-name: #e8f1da;
  }
  * { margin: 0; padding: 0; box-sizing: border-box; }
  html, body {
    width: 1200px; height: 969px; overflow: hidden;
    background: var(--page-bg);
    font-family: "Roboto", Arial, sans-serif;
  }
  .card {
    position: absolute; left: 80px; top: 188px;
    width: 1040px; height: 592px;
    border-radius: 30px; overflow: hidden;
    background: var(--card-bg);
    box-shadow: 0 20px 50px rgba(0,0,0,.22);
  }
  .card-art { position: absolute; inset: 0; }
  .brand { position: absolute; left: 54px; top: 74px; }
  .brand-name {
    font-weight: 900; font-size: 44px; letter-spacing: .5px;
    color: var(--brand-green); text-transform: uppercase; line-height: 1;
  }
  .contact {
    position: absolute; right: 54px; top: 292px; text-align: right;
    color: var(--ink-light);
  }
  .contact-name { font-size: 38px; font-weight: 400; letter-spacing: 1px; color: var(--ink-name); text-transform: uppercase; }
  .contact-role { font-size: 27px; margin-top: 8px; }
  .contact-list { list-style: none; margin-top: 36px; }
  .contact-list li {
    display: flex; justify-content: flex-end; align-items: center;
    gap: 18px; font-size: 25px; height: 40px;
  }
  .contact-list svg { width: 26px; height: 26px; }
</style>
</head>
<body>
  <div class="card">
    <svg class="card-art" viewBox="0 0 1040 592" width="1040" height="592" aria-hidden="true">
      <defs>
        <linearGradient id="band" x1="0" y1="1" x2="1" y2="0">
          <stop offset="0" stop-color="#2c7419"/>
          <stop offset=".6" stop-color="#4f9a22"/>
          <stop offset="1" stop-color="#6fb02e"/>
        </linearGradient>
      </defs>
      <path d="M0 560 C300 520 640 280 1040 10 L1040 592 L0 592 Z" fill="#8cc63f" opacity=".55"/>
      <path d="M0 592 C310 560 660 310 1040 40 L1040 592 Z" fill="url(#band)"/>
      <g class="offer-badge">
        <circle cx="92" cy="500" r="66" fill="#2c7419"/>
        <circle cx="92" cy="500" r="42" fill="#8cc63f"/>
        <path id="badgeArc" d="M92 500 m-54 0 a54 54 0 1 1 108 0 a54 54 0 1 1 -108 0" fill="none"/>
        <text font-family="Roboto, Arial, sans-serif" font-weight="700" font-size="13" fill="#f3f7ec" letter-spacing="1">
          <textPath href="#badgeArc">FREE 30 MINUTE CONSULTATION •</textPath>
        </text>
        <text x="92" y="496" text-anchor="middle" font-family="Roboto, Arial, sans-serif" font-weight="900" font-size="14" fill="#ffffff">SPECIAL</text>
        <text x="92" y="514" text-anchor="middle" font-family="Roboto, Arial, sans-serif" font-weight="900" font-size="14" fill="#ffffff">OFFER!</text>
      </g>
    </svg>

    <div class="brand">
      <p class="brand-name">Liberty Money Coaching</p>
    </div>

    <div class="contact">
      <p class="contact-name">Daniel R. Hayes</p>
      <p class="contact-role">Personal Financial Coach</p>
      <ul class="contact-list">
        <li>(205) 555-0187
          <svg viewBox="0 0 24 24"><rect x="6" y="2" width="12" height="20" rx="2" fill="none" stroke="#fff" stroke-width="2"/><circle cx="12" cy="18" r="1.3" fill="#fff"/></svg>
        </li>
        <li>daniel@steadymoneypath.com
          <svg viewBox="0 0 24 24"><rect x="3" y="6" width="18" height="13" fill="#fff"/><path d="M3 6 L12 13 L21 6" fill="none" stroke="#4f9a22" stroke-width="1.6"/></svg>
        </li>
        <li>www.steadymoneypath.com
          <svg viewBox="0 0 24 24"><circle cx="12" cy="12" r="9" fill="#fff"/><path d="M3 12 H21 M12 3 C8 7 8 17 12 21 M12 3 C16 7 16 17 12 21" fill="none" stroke="#4f9a22" stroke-width="1.4"/></svg>
        </li>
      </ul>
    </div>
  </div>
</body>
</html>
```